LEARN Business Skills so you can Earn a good living

size of the poster is 8”x 10.75" plus 0.25" bleed.
Please leave 1 inch on the bottoum for footer
I want a design a poster that will attract people's attention.
I appreciate a creative ad however the ad should not take away from being able to clearly read the text.
-I also appreciate a simple creative ad that is not too busy.
-you can use graphics, vectors, or pictures of real people.
-however, if you use real people it should be a white male that is wearing a white shirt and look like a professional person.

Target Market(s)

Potential young business people

Industry/Entity Type

education

Requirements
Must have
• easy to read the text
Nice to have
• I would like a "creative" simple ad that is easy to be read
Should not have
• pictures of women

```html
<!DOCTYPE html>
<html lang="en">
<head>
<meta charset="utf-8">
<title>Learn It To Earn It – Business Enrichment Course</title>
<link href="https://fonts.googleapis.com/css2?family=Poppins:wght@300;400;600;700;800&display=swap" rel="stylesheet">
<style>
  :root {
    --canvas: #e6e6e6;
    --paper: #ffffff;
    --ink: #1f1f1f;
    --band: #252525;
    --line: #9a9a9a;
    --icon-fill: #6e6e6e;
    --white: #ffffff;
    --photo-light: #f2f2f2;
    --photo-mid: #d6d6d6;
  }
  * { margin: 0; padding: 0; box-sizing: border-box; }
  html, body { width: 800px; height: 1200px; overflow: hidden; }
  body { background: var(--canvas); font-family: "Poppins", sans-serif; color: var(--ink); position: relative; }

  .poster { position: absolute; left: 10px; top: 80px; width: 780px; height: 1040px; background: var(--paper); overflow: hidden; }

  .hero-photo {
    position: absolute; left: 0; top: 150px; width: 780px; height: 555px;
    background: linear-gradient(90deg, rgba(242,242,242,0) 0%, rgba(220,220,220,0.5) 40%, var(--photo-light) 60%, #e3e3e3 100%);
  }
  .person-photo {
    position: absolute; left: 367px; top: 196px; width: 413px; height: 509px;
    background: linear-gradient(180deg, #e4e4e4 0%, #f3f3f3 45%, var(--photo-mid) 100%);
  }

  .headline { position: absolute; left: 42px; line-height: 1; white-space: nowrap; letter-spacing: -2px; }
  .headline b { font-weight: 800; }
  .headline span { font-weight: 300; }
  .headline--learn { top: 49px; font-size: 160px; }
  .headline--earn { top: 195px; font-size: 100px; }

  .rule { position: absolute; left: 44px; width: 410px; height: 1px; background: var(--line); }
  .rule--top { top: 314px; }
  .rule--bottom { top: 514px; }

  .course-title { position: absolute; left: 42px; top: 342px; font-size: 50px; font-weight: 800; line-height: 51px; letter-spacing: 0.3px; }
  .tagline { position: absolute; left: 43px; top: 548px; font-size: 30px; font-weight: 700; line-height: 35px; }

  .footer-band { position: absolute; left: 0; top: 705px; width: 780px; height: 335px; background: var(--band); color: var(--white); }

  .skills-frame { position: absolute; left: 53px; top: 62px; width: 674px; height: 152px; border: 1.5px solid var(--line); border-radius: 18px; }
  .skills-label {
    position: absolute; left: 94px; top: 38px; width: 591px; height: 44px;
    background: var(--white); color: var(--ink); border-radius: 22px;
    font-size: 29px; font-weight: 700; text-align: center; line-height: 46px; letter-spacing: 0.3px;
  }
  .skill { position: absolute; top: 100px; width: 228px; text-align: center; }
  .skill--job { left: 48px; }
  .skill--business { left: 276px; }
  .skill--salary { left: 504px; }
  .skill svg { display: block; margin: 0 auto; }
  .skill-text { font-size: 19px; font-weight: 700; line-height: 22px; margin-top: 4px; }
  .skill-divider { position: absolute; top: 112px; width: 1px; height: 96px; background: var(--line); }

  .topics { position: absolute; left: 0; top: 238px; width: 780px; text-align: center; font-size: 11.5px; font-weight: 400; line-height: 14.5px; text-transform: uppercase; }
</style>
</head>
<body>
  <main class="poster">
    <div class="hero-photo" role="img" aria-label="Softly blurred bright office interior in greyscale"></div>
    <div class="person-photo" role="img" aria-label="Photo of a smiling professional man in glasses, white shirt and dark tie, talking on a phone with an open hand gesture"></div>

    <h1>
      <div class="headline headline--learn"><b>LEARN</b> <span>IT</span></div>
      <div class="headline headline--earn"><span>TO</span> <b>EARN</b> <span>IT</span></div>
    </h1>

    <div class="rule rule--top"></div>
    <h2 class="course-title">BUSINESS<br>ENRICHMENT<br>COURSE</h2>
    <div class="rule rule--bottom"></div>
    <p class="tagline">A proven success of<br>helping people in their<br>livelihoods</p>

    <section class="footer-band">
      <div class="skills-frame"></div>
      <div class="skills-label">BUSINESS SKILLS THAT WILL HELP YOU</div>

      <div class="skill skill--job">
        <svg width="54" height="54" viewBox="0 0 54 54" aria-hidden="true">
          <circle cx="27" cy="27" r="26" fill="var(--icon-fill)" stroke="#cfcfcf" stroke-width="1.5"/>
          <g fill="none" stroke="#fff" stroke-width="1.6">
            <rect x="16" y="14" width="22" height="16" rx="2"/>
            <circle cx="27" cy="27" r="6"/>
            <path d="M23 32 l-2 9 l6-3 l6 3 l-2-9"/>
            <path d="M20 19h3M25 19h4M31 19h3"/>
          </g>
        </svg>
        <p class="skill-text">Get a<br>quality job</p>
      </div>
      <div class="skill-divider" style="left:276px"></div>

      <div class="skill skill--business">
        <svg width="54" height="54" viewBox="0 0 54 54" aria-hidden="true">
          <circle cx="27" cy="27" r="26" fill="var(--icon-fill)" stroke="#cfcfcf" stroke-width="1.5"/>
          <g fill="none" stroke="#fff" stroke-width="1.6">
            <rect x="14" y="31" width="5" height="8"/>
            <rect x="21" y="27" width="5" height="12"/>
            <rect x="28" y="23" width="5" height="16"/>
            <rect x="35" y="19" width="5" height="20"/>
            <path d="M13 27 L22 20 L28 22 L39 13"/>
            <path d="M34 13 h5 v5"/>
          </g>
        </svg>
        <p class="skill-text">Start/grow<br>your business</p>
      </div>
      <div class="skill-divider" style="left:504px"></div>

      <div class="skill skill--salary">
        <svg width="54" height="54" viewBox="0 0 54 54" aria-hidden="true">
          <circle cx="27" cy="27" r="26" fill="var(--icon-fill)" stroke="#cfcfcf" stroke-width="1.5"/>
          <g fill="none" stroke="#fff" stroke-width="1.6">
            <rect x="15" y="25" width="24" height="13" rx="1.5"/>
            <circle cx="27" cy="31.5" r="3"/>
            <path d="M15 41 h24"/>
            <path d="M17 21 L24 16 L29 19 L37 12"/>
            <path d="M33 12 h4 v4"/>
          </g>
        </svg>
        <p class="skill-text">Increase your<br>salary</p>
      </div>

      <p class="topics">
        Business Admiistration &nbsp;|&nbsp; Small Business Management &nbsp;|&nbsp; Finance | Investments &nbsp;|&nbsp; Computers &nbsp;|&nbsp; Accounting<br>
        Sales &nbsp;|&nbsp; Marketing &nbsp;|&nbsp; Project Management Interviewing Skills &nbsp;|&nbsp; Business Law &nbsp;|&nbsp; Negotiation &nbsp;|&nbsp; Public Speaking<br>
        Import/Export &nbsp;|&nbsp; Information Technoloy &nbsp;|&nbsp; Distribution &nbsp;|&nbsp; Marketing &nbsp;|&nbsp; LedgerPro &nbsp;|&nbsp; Real Estate<br>
        Health Care-Management &nbsp;|&nbsp; MarketHub
      </p>
    </section>
  </main>
</body>
</html>
```